web page design with coding

We are a start up insurance agency who needs to design a full functional web page. we recently did a postcard design though drawkettle I will upload the final project for you to see the color scheme/font we would like to continue to use. I also have a rough draft of verbage I would like our website to have. I will upload that as well.

Reason: I am sorry but the person who will make the final decision on the website is out of the country at the moment and will make the final decision when he returns.

Industry/Entity Type

Insurance

Coding

Coded - Design and coding required

```html
<!DOCTYPE html>
<html lang="en">
<head>
<meta charset="utf-8">
<title>Claremont Insurance Group</title>
<link href="https://fonts.googleapis.com/css2?family=Roboto:wght@400;500;700&family=Oswald:wght@400;500&display=swap" rel="stylesheet">
<style>
:root{
  --navy:#1a3a6c;
  --navy-dark:#16305a;
  --green:#2d7e3f;
  --green-bright:#3fb64c;
  --grey-band:#eeeeef;
  --text:#333333;
  --muted:#777777;
  --white:#ffffff;
  --photo-sky:#b9c3cc;
  --photo-warm:#8d7a6a;
}
*{margin:0;padding:0;box-sizing:border-box}
html,body{width:1200px;height:2452px;overflow:hidden}
body{font-family:'Roboto',Arial,sans-serif;color:var(--text);background:var(--white);position:relative}
.abs{position:absolute}
section,header,footer{position:absolute;left:0;width:1200px}

/* top bar */
.topbar{top:0;height:44px;background:var(--navy);color:var(--white);font-size:13px}
.topbar .contact-line{left:94px;top:14px;display:flex;gap:26px;align-items:center}
.topbar .contact-line span{display:flex;align-items:center;gap:7px}
.topbar .social-dots{right:94px;top:15px;display:flex;gap:6px}
.topbar .social-dots i{width:13px;height:13px;background:var(--white);display:block;border-radius:2px}

/* header */
.site-header{top:44px;height:90px;background:var(--white);box-shadow:0 2px 4px rgba(0,0,0,.08);z-index:2}
.brand{left:90px;top:18px;width:112px;color:var(--navy);font-weight:700;font-size:17px;line-height:21px}
.main-nav{top:35px;left:0;width:100%;font-size:15px;font-weight:400;color:#333}
.main-nav a{position:absolute;text-decoration:none;color:inherit;letter-spacing:.2px;white-space:nowrap}
.main-nav a.active{color:var(--green)}

/* hero */
.hero{top:134px;height:587px;background:linear-gradient(135deg,var(--photo-sky) 0%,#d9dde0 40%,var(--photo-warm) 75%,#5d7a4a 100%)}
.hero-caption{left:90px;top:461px;width:455px;height:108px;background:rgba(255,255,255,.78);padding:20px 28px 0}
.hero-caption h1{font-family:'Oswald',Arial,sans-serif;font-weight:500;color:var(--navy);font-size:30px;line-height:38px;letter-spacing:0;white-space:nowrap}
.hero-caption p{font-family:'Oswald',Arial,sans-serif;font-weight:400;color:#333;font-size:21px;line-height:30px;white-space:nowrap}
.slider-arrow{top:523px;width:36px;height:36px;border-radius:50%;background:rgba(40,40,40,.75)}
.quote-box{left:827px;top:214px;width:285px;height:373px;background:var(--navy)}
.quote-box .quote-title{height:52px;background:var(--white);text-align:center;font-size:17px;font-weight:500;line-height:52px;color:#222;letter-spacing:.3px}
.field{position:absolute;left:17px;width:250px;height:42px;background:var(--white);border-radius:4px;font-size:13px;color:#333;padding:0 13px;line-height:42px}
.field .caret{position:absolute;right:16px;top:18px}
.btn-submit{position:absolute;left:17px;top:301px;width:250px;height:43px;border-radius:4px;background:linear-gradient(#47c256,#2d9b3c);color:var(--white);font-size:15px;text-align:center;line-height:43px}

/* welcome */
.welcome{top:721px;height:190px;background:var(--green);color:var(--white);text-align:center}
.welcome h2{margin-top:38px;font-size:26px;font-weight:500;letter-spacing:.3px}
.welcome p{margin:18px auto 0;width:1020px;font-size:15px;line-height:24.5px}

/* features */
.features{top:911px;height:322px;background:var(--grey-band)}
.feature{position:absolute;top:80px;width:300px;text-align:center}
.feature svg{display:block;margin:0 auto}
.feature h3{margin-top:22px;font-size:17px;font-weight:500;color:#222;letter-spacing:.3px}
.feature p{margin:14px auto 0;width:270px;font-size:13px;line-height:21px;color:var(--muted)}

/* agents */
.agents{top:1233px;height:346px;background:var(--white)}
.agent-photo{left:92px;top:64px;width:279px;height:237px;background:linear-gradient(160deg,#d6dbe0,#8a949e 55%,#2c2f36)}
.agents h2{left:415px;top:72px;font-size:25px;font-weight:500;color:#222;letter-spacing:.5px}
.agents .copy{left:415px;top:114px;width:690px;font-size:12.8px;line-height:20px;color:#333}
.agents .copy p+p{margin-top:13px}
.btn-read{left:412px;top:264px;width:98px;height:33px;background:var(--green);color:var(--white);font-size:12px;line-height:33px;text-align:center;border-radius:2px}

/* insurance split */
.split{top:1579px;height:316px}
.split .panel{position:absolute;top:0;height:316px;color:var(--white)}
.panel.business{left:0;width:600px;background:var(--navy)}
.panel.personal{left:600px;width:600px;background:var(--green)}
.panel h2{position:absolute;left:90px;top:58px;font-size:25px;font-weight:500;letter-spacing:.3px}
.panel.personal h2{left:81px}
.panel p{position:absolute;left:90px;top:101px;width:440px;font-size:13px;font-weight:500;line-height:24.5px}
.panel.personal p{left:81px;text-align:justify;width:432px}
.btn-outline{position:absolute;left:90px;top:237px;width:105px;height:38px;border:1.5px solid var(--white);border-radius:3px;font-size:15px;line-height:35px;text-align:center}
.panel.personal .btn-outline{left:82px}

/* blog */
.blog{top:1895px;height:286px;background:var(--grey-band)}
.blog h2{left:90px;top:55px;font-size:20px;font-weight:400;color:#222}
.blog h2 span{color:#2a7fb8}
.blog .nav-arrows{left:1086px;top:58px}
.post-img{top:105px;width:162px;height:132px}
.post-title{font-size:14.5px;font-weight:500;color:#222}
.post-date{font-size:12px;color:#444}
.post-text{width:306px;font-size:11.5px;line-height:20px;color:#444}
.post-more{font-size:12px;color:var(--navy)}

/* footer */
.site-footer{top:2181px;height:271px;background:var(--navy);color:var(--white)}
.site-footer h4{position:absolute;top:39px;font-size:15px;font-weight:500;letter-spacing:.3px}
.site-footer .small{position:absolute;font-size:12.5px;line-height:20px}
.newsletter-input{left:659px;top:128px;width:170px;height:40px;background:var(--white);font-size:11px;color:#999;line-height:40px;padding-left:14px}
.btn-signup{left:829px;top:128px;width:80px;height:40px;background:var(--green);font-size:16px;line-height:40px;text-align:center}
.social-square{top:80px;width:34px;height:34px;background:var(--white);border-radius:3px}
.footer-rule{left:0;top:212px;width:1200px;height:1px;background:rgba(255,255,255,.18)}
.copyright{left:0;top:234px;width:1200px;text-align:center;font-size:13px}
</style>
</head>
<body>

<header class="topbar">
  <div class="abs contact-line">
    <span>
      <svg width="12" height="12" viewBox="0 0 12 12"><rect width="12" height="12" rx="2" fill="#fff"/><path d="M3.5 2.6l1.5 1.6-.8 1a5 5 0 0 0 1.8 1.8l1-.8 1.6 1.5-.9 1.3C5.6 9 3 6.4 2.2 3.5z" fill="#1a3a6c"/></svg>
      : (555) 014-2290
    </span>
    <span>
      <svg width="13" height="10" viewBox="0 0 13 10"><rect width="13" height="10" rx="1" fill="#fff"/><path d="M1 1.2l5.5 4.3L12 1.2" stroke="#1a3a6c" stroke-width="1.2" fill="none"/></svg>
      : hello@claremontig.example
    </span>
  </div>
  <div class="abs social-dots"><i></i><i></i><i></i><i></i></div>
</header>

<header class="site-header">
  <div class="abs brand">Claremont Insurance Group</div>
  <nav class="main-nav abs">
    <a class="active" style="left:391px">HOME</a>
    <a style="left:479px">ABOUT US</a>
    <a style="left:597px">AGENTS</a>
    <a style="left:701px">PRODUCTS AND SERVICES</a>
    <a style="left:937px">NEWS</a>
    <a style="left:1025px">CONTACTS</a>
  </nav>
</header>

<section class="hero">
  <div class="abs" style="inset:0" role="img" aria-label="Photo of a smiling family of three standing in front of a modern white house"></div>
  <div class="abs hero-caption">
    <h1>CLAREMONT INSURANCE GROUP</h1>
    <p>Neque porro quisquam est qui dolorem ipsum</p>
  </div>
  <div class="abs slider-arrow" style="left:729px">
    <svg width="36" height="36" viewBox="0 0 36 36"><path d="M20 11l-7 7 7 7" stroke="#fff" stroke-width="2.4" fill="none"/></svg>
  </div>
  <div class="abs slider-arrow" style="left:768px">
    <svg width="36" height="36" viewBox="0 0 36 36"><path d="M16 11l7 7-7 7" stroke="#fff" stroke-width="2.4" fill="none"/></svg>
  </div>
  <form class="abs quote-box">
    <div class="quote-title">INSURANCE QUOTES</div>
    <div class="field" style="top:79px">Name</div>
    <div class="field" style="top:136px">Phone</div>
    <div class="field" style="top:192px">Email id</div>
    <div class="field" style="top:246px">Type of Insurance
      <svg class="caret" width="10" height="6" viewBox="0 0 10 6"><path d="M0 0h10L5 6z" fill="#444"/></svg>
    </div>
    <div class="btn-submit">SUBMIT</div>
  </form>
</section>

<section class="welcome">
  <h2>WELCOME TO CLAREMONT INSURANCE GROUP</h2>
  <p>Claremont Insurance Group has joined with regional &amp; national insurance companies to provide quality products and superior service.&nbsp; We take the time to discuss options and coverages, not to just sell insurance products. We strive to educate you in the decision making process to become an informed consumer We specialize in commercial business &amp; personal insurance. We are committed to providing personal attention to all your insurance needs.</p>
</section>

<section class="features">
  <div class="feature" style="left:80px">
    <svg width="36" height="40" viewBox="0 0 36 40"><circle cx="18" cy="11" r="9" fill="#1a3a6c"/><path d="M2 40c0-11 7-17 16-17s16 6 16 17z" fill="#1a3a6c"/></svg>
    <h3>WHAT WE DO</h3>
    <p>Lorem Ipsum has been the industry's standard dummy text ever since the 1500s, when an unknown printer took a galley of type</p>
  </div>
  <div class="feature" style="left:445px">
    <svg width="48" height="42" viewBox="0 0 48 42"><g fill="#1a3a6c"><circle cx="17" cy="20" r="11"/><g stroke="#1a3a6c" stroke-width="5"><path d="M17 4v32M1 20h32M6 9l22 22M28 9L6 31"/></g><circle cx="36" cy="11" r="6"/><g stroke="#1a3a6c" stroke-width="3"><path d="M36 2v18M27 11h18"/></g><circle cx="36" cy="32" r="6"/><g stroke="#1a3a6c" stroke-width="3"><path d="M36 23v18M27 32h18"/></g></g><circle cx="17" cy="20" r="4" fill="#eeeeef"/><circle cx="36" cy="11" r="2.2" fill="#eeeeef"/><circle cx="36" cy="32" r="2.2" fill="#eeeeef"/></svg>
    <h3>PRODUCTS AND SERVICES</h3>
    <p>Lorem Ipsum has been the industry's standard dummy text ever since the 1500s, when an unknown printer took a galley of type</p>
  </div>
  <div class="feature" style="left:810px">
    <svg width="34" height="44" viewBox="0 0 34 44"><path d="M0 0h23l11 11v33H0z" fill="#1a3a6c"/><path d="M23 0v11h11" fill="#4d6b99"/><path d="M7 20h20M7 27h20M7 34h20" stroke="#eeeeef" stroke-width="2.5"/></svg>
    <h3>INSURANCE</h3>
    <p>Lorem Ipsum has been the industry's standard dummy text ever since the 1500s, when an unknown printer took a galley of type</p>
  </div>
</section>

<section class="agents">
  <div class="abs agent-photo" role="img" aria-label="Portrait photo of a smiling agent in a dark suit and red tie"></div>
  <h2 class="abs">AGENTS</h2>
  <div class="abs copy">
    <p>Established in 2015, Claremont Insurance Group is a full service independent insurance agency.&nbsp; Our licensed agents have the experience to custom tailor a program to meet your specific needs &amp; our professional support staff will provide you with top notch customer service to help ease the burden of managing your insurance program.</p>
    <p>At Claremont Insurance Group, we are independent insurance agents. As independent agents, we do not work for any one insurance company; we sell coverage from several different companies. This allows us to focus on providing you with the&nbsp; right amount of insurance and the right type of coverage for your unique needs.</p>
  </div>
  <div class="abs btn-read">READ MORE</div>
</section>

<section class="split">
  <div class="panel business">
    <h2>BUSINESS INSURANCE</h2>
    <p>Claremont Insurance Group has joined with regional &amp; national insurance companies to provide quality products and superior service.&nbsp; We take the time to discuss options and coverages, not to just sell insurance products. We strive to educate you in the decision making process to become an informed consumer.</p>
    <div class="btn-outline">View more</div>
  </div>
  <div class="panel personal">
    <h2>PERSONAL INSURANCE</h2>
    <p>Claremont Insurance Group has joined with regional &amp; national insurance companies to provide quality products and superior service.&nbsp; We take the time to discuss options and coverages, not to just sell insurance products. We strive to educate you in the decision making process to become an informed consumer.</p>
    <div class="btn-outline">View more</div>
  </div>
</section>

<section class="blog">
  <h2 class="abs">LATEST <span>BLOG</span></h2>
  <svg class="abs nav-arrows" width="26" height="16" viewBox="0 0 26 16"><path d="M8 2L2 8l6 6M18 2l6 6-6 6" stroke="#222" stroke-width="2" fill="none"/></svg>

  <div class="abs post-img" style="left:90px;background:linear-gradient(135deg,#dfe3e6,#8d97a1 60%,#4a5561)" role="img" aria-label="Photo of colleagues reviewing documents at a desk"></div>
  <div class="abs post-title" style="left:270px;top:110px">Nemo Enim Ipsam Volup</div>
  <div class="abs post-date" style="left:270px;top:136px">09-07-2016</div>
  <div class="abs post-text" style="left:270px;top:156px">Lorem Ipsum has been the industry's standard dummy text ever since the 1500s, when an unknown printer took a galley of type and scrambled it to make a type specimen book.</div>
  <div class="abs post-more" style="left:270px;top:220px">Read More &gt;&gt;</div>

  <div class="abs post-img" style="left:625px;background:linear-gradient(135deg,#3f6f8f,#a9c3d3 55%,#e2e8ec)" role="img" aria-label="Photo of a tablet showing an insurance page"></div>
  <div class="abs post-title" style="left:806px;top:104px">Nemo Enim Ipsam Volup</div>
  <div class="abs post-date" style="left:806px;top:130px">09-07-2016</div>
  <div class="abs post-text" style="left:806px;top:150px">Lorem Ipsum has been the industry's standard dummy text ever since the 1500s, when an unknown printer took a galley of type and scrambled it to make a type specimen book.</div>
  <div class="abs post-more" style="left:806px;top:214px">Read More &gt;&gt;</div>
</section>

<footer class="site-footer">
  <h4 style="left:90px">CONTACT US</h4>
  <div class="small" style="left:90px;top:69px">42 Linden Avenue 3rd Floor<br>Brookfield, NY&nbsp; 10020,&nbsp; USA</div>
  <div class="abs" style="left:94px;top:125px;display:flex;align-items:center;gap:12px;font-size:17px">
    <svg width="18" height="18" viewBox="0 0 18 18"><path d="M4 1.5l3 3.2-1.5 2a9 9 0 0 0 5.8 5.8l2-1.5 3.2 3-1.8 2.5C8.6 16.5 1.5 9.4 1.5 3.3z" stroke="#fff" stroke-width="1.3" fill="none"/></svg>
    (555) 014-7731
  </div>
  <div class="abs" style="left:94px;top:153px;display:flex;align-items:center;gap:12px;font-size:13px">
    <svg width="18" height="13" viewBox="0 0 18 13"><rect x=".7" y=".7" width="16.6" height="11.6" fill="none" stroke="#fff" stroke-width="1.3"/><path d="M1 1l8 6.5L17 1" stroke="#fff" stroke-width="1.3" fill="none"/></svg>
    office@claremontig.example
  </div>

  <h4 style="left:343px">LATEST TWEET'S</h4>
  <div class="abs" style="left:347px;top:76px;width:16px;height:16px;background:#fff;border-radius:2px"></div>
  <div class="small" style="left:381px;top:69px;width:200px;font-size:11.5px;line-height:19.5px">Phasellus porta. Fusce susct varius mi. Cum sociis natoque penabus et magnis dis parturient montes, nas-cetur ridiculus mus. See more here http://t.co/k4Rqzp72mW</div>

  <h4 style="left:657px">NEWSLETTER</h4>
  <div class="small" style="left:659px;top:70px;width:260px;font-size:11.5px;line-height:20px">Excepteur sint occaecat cupidatat non proident, sunt in culpa qui officia deserunt mollit anim</div>
  <div class="abs newsletter-input">Enter your email address</div>
  <div class="abs btn-signup">Sign Up</div>

  <h4 style="left:971px">SOCIAL MEDIA</h4>
  <div class="abs social-square" style="left:972px"></div>
  <div class="abs social-square" style="left:1025px"></div>
  <div class="abs social-square" style="left:1078px"></div>

  <div class="abs footer-rule"></div>
  <div class="abs copyright">2016&nbsp; All Rights Reserved.</div>
</footer>

</body>
</html>
```